Read Your Frame
Stationary
Project: Read Your Frame
Read Your Frame - Health
Creative Brief
Use specific fonts
Whatever fonts look best!
Professional
Linus Ferrick
Body Composition Specialist/ Personal Trainer
Dont put address.
linusferrick@mailvex.com
ReadYourFrameMakeup.com
We use a state of the art body composition analyzer to accurately determine total body fat, essential fat, non essential fat, reserve fat, total body water, and lean mass. It's fast, non-invasive, and comparable to the Gold Standard. To find out more visit our website or call us.

```html
<!DOCTYPE html>
<html lang="en">
<head>
<meta charset="utf-8">
<title>Read Your Frame – Stationery</title>
<link rel="stylesheet" href="https://fonts.googleapis.com/css2?family=Arimo:wght@400;700&display=swap">
<style>
  :root {
    --bg: #e9e6e1;
    --card-light: #ffffff;
    --card-dark: #141416;
    --card-dark-edge: #2a2b2f;
    --brand-blue: #1e8fd6;
    --ink: #2b2b2b;
    --ink-soft: #666a70;
    --ink-on-dark: #e4e6ea;
    --shade: #c9ccd1;
  }
  * { box-sizing: border-box; margin: 0; padding: 0; }
  html, body { width: 1200px; height: 911px; overflow: hidden; }
  body {
    background: var(--bg);
    font-family: "Arimo", Arial, sans-serif;
    display: grid;
    grid-template-columns: 500px 500px;
    grid-template-rows: 286px 286px;
    gap: 60px;
    padding: 140px 70px;
  }
  .card {
    position: relative;
    border-radius: 10px;
    overflow: hidden;
    box-shadow: 0 6px 18px rgba(0,0,0,.18);
  }
  .card--light { background: var(--card-light); color: var(--ink); }
  .card--dark {
    background: linear-gradient(160deg, var(--card-dark-edge) 0%, var(--card-dark) 55%);
    color: var(--ink-on-dark);
  }
  .edge-band {
    position: absolute; left: 0; right: 0; bottom: 0; height: 10px;
    background: linear-gradient(90deg, var(--shade) 0 55%, var(--brand-blue) 55% 100%);
  }
  .card--dark .edge-band {
    background: linear-gradient(90deg, #3a3c41 0 55%, var(--brand-blue) 55% 100%);
  }
  .brand { display: flex; align-items: center; gap: 10px; }
  .brand__mark {
    width: 14px; height: 14px; background: var(--brand-blue); flex: none;
  }
  .brand__name {
    font-weight: 700;
    font-size: 28px;
    line-height: 1;
    color: var(--brand-blue);
    white-space: nowrap;
  }
  .front .brand { position: absolute; top: 40px; left: 36px; }
  .front .details {
    position: absolute; left: 36px; right: 24px; bottom: 40px;
    display: flex; align-items: flex-start; gap: 14px;
  }
  .person { text-align: right; width: 190px; }
  .person__name { font-size: 19px; font-weight: 700; color: var(--brand-blue); }
  .person__role { font-size: 11px; line-height: 1.45; margin-top: 3px; }
  .divider { width: 1px; align-self: stretch; background: var(--ink-soft); }
  .card--dark .divider { background: #6c7078; }
  .contact { font-size: 11px; line-height: 1.55; }
  .contact__web { color: var(--brand-blue); }
  .card--dark .person { text-align: left; width: auto; }
  .back {
    display: flex; flex-direction: column; align-items: center;
    text-align: center; padding: 30px 34px 0;
  }
  .back .brand__name { font-size: 22px; }
  .back .brand__mark { width: 11px; height: 11px; }
  .back__copy { font-size: 13px; line-height: 1.4; margin-top: 22px; }
  .back__cta { font-size: 13px; font-weight: 700; color: var(--brand-blue); margin-top: 14px; }
  .back__web { font-size: 10px; color: var(--brand-blue); margin-top: 10px; }
</style>
</head>
<body>

  <section class="card card--light front">
    <div class="brand">
      <span class="brand__mark"></span>
      <span class="brand__name">Read Your Frame</span>
    </div>
    <div class="details">
      <div class="person">
        <p class="person__name">Linus Ferrick</p>
        <p class="person__role">Body Composition Specialist<br>Personal Trainer</p>
      </div>
      <span class="divider"></span>
      <div class="contact">
        <p>Phone: 916.555.0142</p>
        <p>Email: linusferrick@mailvex.com</p>
        <p class="contact__web">www.ReadYourFrameMakeup.com</p>
      </div>
    </div>
    <span class="edge-band"></span>
  </section>

  <section class="card card--dark front">
    <div class="brand">
      <span class="brand__mark"></span>
      <span class="brand__name">Read Your Frame</span>
    </div>
    <div class="details">
      <div class="person">
        <p class="person__name">Linus Ferrick</p>
        <p class="person__role">Body Composition Specialist<br>Personal Trainer</p>
      </div>
      <span class="divider"></span>
      <div class="contact">
        <p>Phone: 916.555.0142</p>
        <p>Email: linusferrick@mailvex.com</p>
        <p class="contact__web">www.ReadYourFrameMakeup.com</p>
      </div>
    </div>
    <span class="edge-band"></span>
  </section>

  <section class="card card--light back">
    <div class="brand">
      <span class="brand__mark"></span>
      <span class="brand__name">Read Your Frame</span>
    </div>
    <p class="back__copy">We use a state of the art body composition analyzer to accurately determine total body fat, essential fat, non essential fat, reserve fat, total body water, and lean mass. It's fast, non-invasive, and comparable to the Gold Standard.</p>
    <p class="back__cta">To find out more visit our website or call us</p>
    <p class="back__web">www.ReadYourFrameMakeup.com</p>
  </section>

  <section class="card card--dark back">
    <div class="brand">
      <span class="brand__mark"></span>
      <span class="brand__name">Read Your Frame</span>
    </div>
    <p class="back__copy">We use a state of the art body composition analyzer to accurately determine total body fat, essential fat, non essential fat, reserve fat, total body water, and lean mass. It's fast, non-invasive, and comparable to the Gold Standard.</p>
    <p class="back__cta">To find out more visit our website or call us</p>
    <p class="back__web">www.ReadYourFrameMakeup.com</p>
  </section>

</body>
</html>
```